Business Card Design for Varomir Facility Services

We are looking for a Business Card Design for the Company "Varomir Facility Services."
Front side:
- Company Logo (small)
- Company Name, address, pohone, website and personal data.
- white background, for text e.g. company colors (blue or green like in the logo)
Please use following data:
Company data:
Varomir Facility Services Kostelac
Birkenhaldweg 14
6342 Brunnwil
www.varomir-fs.ch
Person data:
Tarik Kostelac
Geschäftsführer
+41 76 519 47 83
info@varomir-fs.ch
Back side:
could be colored in blue or green
please use a big logo sing and some smaller icons to say what is all beeing offered in facility services, like cleaning, maintenance cleaning
industrial cleaning, caretaking, gardening, disposal. There is no need for everyone of the icons if there are similar or an icon is standing for more of them.
colors to use:
blue: HEX 246BB0
green: HEX 52B33E

```html
<!DOCTYPE html>
<html lang="de">
<head>
<meta charset="utf-8">
<title>Varomir Facility Services – Visitenkarte</title>
<link rel="stylesheet" href="https://fonts.googleapis.com/css2?family=Lato:wght@400;700&display=swap">
<style>
  :root {
    --blue: #246BB0;
    --green: #52B33E;
    --ink: #222;
    --paper: #ffffff;
    --stage: #e6e6e6;
    --rule: #c9c9c9;
    --rule-light: rgba(255,255,255,0.55);
  }
  * { margin: 0; padding: 0; box-sizing: border-box; }
  html, body { width: 1200px; height: 802px; overflow: hidden; }
  body {
    background: var(--stage);
    font-family: "Lato", sans-serif;
    position: relative;
  }
  .card {
    position: absolute;
    top: 274px;
    width: 443px;
    height: 265px;
    box-shadow: 0 3px 8px rgba(0,0,0,0.25);
  }
  .card--front { left: 136px; background: var(--paper); }
  .card--back { left: 624px; background: var(--blue); }

  /* company name */
  .company-name {
    position: absolute;
    display: flex;
    align-items: center;
    gap: 9px;
    font-weight: 700;
    font-size: 21px;
    line-height: 1;
    white-space: nowrap;
  }
  .company-name__square { width: 12px; height: 12px; }

  .card--front .company-name { right: 32px; top: 82px; color: var(--blue); }
  .card--front .company-name__square { background: var(--blue); }
  .card--back .company-name { left: 0; right: 0; top: 118px; justify-content: center; color: #fff; font-size: 23px; }
  .card--back .company-name__square { background: #fff; }

  /* front person block */
  .person { position: absolute; left: 28px; top: 151px; right: 32px; }
  .person__name {
    display: flex; align-items: center; gap: 6px;
    color: var(--blue); font-weight: 700; font-size: 16.5px; line-height: 1;
  }
  .person__name::after { content: ""; flex: 1; height: 1px; background: var(--rule); }
  .person__role { font-size: 13px; color: var(--ink); margin-top: 1px; }

  .contact { position: absolute; left: 28px; top: 199px; list-style: none; font-size: 13px; color: var(--ink); }
  .contact li { display: flex; align-items: center; gap: 5px; height: 16px; }
  .contact svg { width: 10px; height: 10px; fill: var(--blue); }

  .address { position: absolute; right: 32px; top: 183px; text-align: right; font-size: 13px; line-height: 15.6px; font-style: normal; color: var(--ink); }
  .address__company { color: var(--blue); }

  /* back services */
  .service-mark { position: absolute; left: 71px; right: 85px; top: 169px; height: 42px; display: flex; align-items: center; gap: 8px; }
  .service-mark__rule { flex: 1; height: 1px; background: var(--rule-light); }
  .service-mark__icon { width: 42px; height: 42px; border-radius: 50%; border: 2px solid #fff; background: var(--blue); }
  .services { position: absolute; left: 0; right: 0; top: 216px; text-align: center; color: #fff; font-size: 11.6px; line-height: 14px; }
  .services span { margin: 0 3px; }
</style>
</head>
<body>

<section class="card card--front" aria-label="Vorderseite">
  <p class="company-name">
    <span class="company-name__square"></span>
    <span>Varomir Facility Services</span>
  </p>

  <div class="person">
    <p class="person__name">TARIK KOSTELAC</p>
    <p class="person__role">Geschäftsführer</p>
  </div>

  <ul class="contact">
    <li><svg viewBox="0 0 10 10"><path d="M1 3c0-1 1-2 4-2s4 1 4 2v1H7V3H3v1H1z M2 5h6l1 4H1z"/></svg>+41 76 519 47 83</li>
    <li><svg viewBox="0 0 10 10"><path d="M0 2h10v6H0z M0 2l5 3.5L10 2" stroke="#fff" stroke-width="0.8"/></svg>info@varomir-fs.ch</li>
    <li><svg viewBox="0 0 10 10"><circle cx="5" cy="5" r="4.5"/></svg>www.varomir-fs.ch</li>
  </ul>

  <address class="address">
    <span class="address__company">Varomir Facility Services<br>Kostelac</span><br>
    Birkenhaldweg 14<br>
    6342 Brunnwil
  </address>
</section>

<section class="card card--back" aria-label="Rückseite">
  <p class="company-name">
    <span class="company-name__square"></span>
    <span>Varomir Facility Services</span>
  </p>

  <div class="service-mark">
    <span class="service-mark__rule"></span>
    <span class="service-mark__icon" role="img" aria-label="Icon: Reinigungskraft mit Bodenmaschine"></span>
    <span class="service-mark__rule"></span>
  </div>

  <p class="services">
    CLEANING<span>|</span>MAINTENANCE CLEANING<span>|</span>INDUSTRIAL CLEANING<br>
    CARETAKING<span>|</span>GARDENING<span>|</span>DISPOSAL
  </p>
</section>

</body>
</html>
```